Evaporative Air Conditioning Summer Service

Would like to design a flyer to send out in an email to existing clients to promote a Pre-summer service for Evaporative Air Conditioners
Cost will be $110.00 inc gst
Tasks included in service are
- Inspection and clean of pads
- Inspection and check float valve, water pump, fan, motor, bearings, drain
- Clean basin
- Supply of bacterial tablet
- Inspect overall condition of unit
- Any repairs if required will be quoted
Please see files attached of a previous very basic flyer I have used for installation and replacement unit costs. This has current contact information
Have also uploaded company logo for use.
Thanks
Plumbing

```html
<!DOCTYPE html>
<html lang="en">
<head>
<meta charset="utf-8">
<title>Harbourline Gas &amp; Plumbing – Pre-Summer Service</title>
<link rel="stylesheet" href="https://fonts.googleapis.com/css2?family=Marcellus&display=swap">
<style>
  :root {
    --navy: #1c1a8a;
    --navy-deep: #12107a;
    --sunshine: #fbd630;
    --crimson: #b50d0d;
    --brick: #b03a2a;
    --ink: #0d0d0d;
    --orange: #f7941d;
    --sky-light: #dce8fb;
    --sky: #7fa8ea;
    --white: #ffffff;
  }
  * { margin: 0; padding: 0; box-sizing: border-box; }
  html, body { width: 848px; height: 1200px; overflow: hidden; background: #ffffff; }
  .flyer {
    position: relative;
    width: 848px;
    height: 1200px;
    overflow: hidden;
    background: var(--sunshine);
    font-family: "Marcellus", serif;
  }
  .header {
    position: absolute; left: 0; top: 0; width: 848px; height: 152px;
    background: linear-gradient(170deg, var(--navy) 0%, var(--navy) 70%, #2a2aa0 100%);
  }
  .brand {
    position: absolute; left: 0; right: 0; top: 30px;
    display: flex; align-items: center; justify-content: center; gap: 18px;
    color: var(--orange);
  }
  .brand-dot { width: 46px; height: 46px; border-radius: 50%; background: var(--orange); }
  .brand-name { line-height: 1; text-align: center; }
  .brand-name .main { display: block; font-size: 58px; letter-spacing: 4px; }
  .brand-name .sub { display: block; font-size: 26px; letter-spacing: 6px; margin-top: 6px; }

  .photo-strip {
    position: absolute; left: 0; top: 150px; width: 848px; height: 202px;
    background: #111111;
  }
  .photo { position: absolute; top: 7px; width: 273px; height: 188px; }
  .photo.vent { left: 7px; background: linear-gradient(135deg, #f4f4f4, #bdbdbd); }
  .photo.indoor-unit { left: 288px; background: linear-gradient(135deg, #f2f4f6, #8fb3c4); }
  .photo.condenser { left: 568px; background: linear-gradient(135deg, #5a7380, #a9754e); }

  .headline {
    position: absolute; left: 0; right: 0; top: 354px;
    text-align: center; font-size: 33px; line-height: 41px; color: var(--crimson);
  }
  .headline .accent { color: var(--navy); }

  .offer {
    position: absolute; left: 20px; top: 458px; width: 430px;
    text-align: center; color: var(--navy-deep); font-size: 21px; line-height: 34px;
  }
  .offer .dark { color: var(--ink); }

  .price-tag {
    position: absolute; left: 508px; top: 492px; width: 324px; height: 102px;
    border-radius: 16px 24px 40px 16px;
    background: linear-gradient(100deg, var(--sky-light) 0%, var(--sky-light) 55%, var(--sky) 100%);
    text-align: center;
  }
  .price-tag .lead { display: block; margin-top: 4px; font-size: 37px; letter-spacing: 2px; color: var(--navy-deep); line-height: 48px; }
  .price-tag .amount { display: block; font-size: 38px; color: var(--ink); line-height: 48px; }

  .call-now {
    position: absolute; left: 0; right: 0; top: 648px;
    text-align: center; font-size: 50px; line-height: 64px; letter-spacing: 2px; color: var(--ink);
  }
  .call-now .label { color: var(--crimson); }

  .tasks-bar {
    position: absolute; left: 116px; top: 726px; width: 616px; height: 74px;
    background: linear-gradient(165deg, #0a0a0a 0%, #111111 60%, #4a4a4a 100%);
    color: var(--brick); font-size: 31px; line-height: 74px; text-align: center;
  }

  .task-list {
    position: absolute; left: 116px; top: 820px; width: 640px; list-style: none;
    color: var(--brick); font-size: 27px; line-height: 38px;
  }
  .task-list li { position: relative; padding-left: 78px; }
  .task-list .tick { position: absolute; left: 0; top: 6px; width: 32px; height: 26px; }

  .footer {
    position: absolute; left: 0; top: 1098px; width: 848px; height: 102px;
    background: linear-gradient(172deg, var(--navy-deep) 0%, var(--navy-deep) 55%, #2626a0 100%);
    color: var(--white);
  }
  .footer .abn { position: absolute; left: 101px; top: 26px; font-size: 18px; }
  .footer .email { position: absolute; left: 101px; top: 64px; font-size: 18px; letter-spacing: 0.5px; }
  .footer .mail-icon { position: absolute; left: 44px; top: 63px; width: 34px; height: 25px; }
  .footer-brand {
    position: absolute; left: 560px; top: 30px;
    display: flex; align-items: center; gap: 10px; color: var(--orange); line-height: 1;
  }
  .footer-brand .brand-dot { width: 22px; height: 22px; }
  .footer-brand .main { display: block; font-size: 28px; letter-spacing: 2px; }
  .footer-brand .sub { display: block; font-size: 13px; letter-spacing: 3px; margin-top: 4px; }
</style>
</head>
<body>
<main class="flyer">
  <header class="header">
    <div class="brand">
      <span class="brand-dot"></span>
      <span class="brand-name"><span class="main">HARBOURLINE</span><span class="sub">GAS &amp; PLUMBING</span></span>
    </div>
  </header>

  <section class="photo-strip">
    <div class="photo vent" role="img" aria-label="Dusty air vent grille and filter under a magnifying glass"></div>
    <div class="photo indoor-unit" role="img" aria-label="Opened indoor air conditioner unit with dusty coil"></div>
    <div class="photo condenser" role="img" aria-label="Outdoor condenser unit with dirt-covered fins"></div>
  </section>

  <h1 class="headline">IS YOUR <span class="accent">AIR CONDITIONER</span> GOING<br>THROUGH THE HARD TIME?</h1>

  <p class="offer">BOOK OUR<br><span class="dark">PRE-SUMMER SERVICE PACKAGE</span><br>AT DISCOUNTED PRICE<br>AND ENJOY<br>THE ALL NEW FRESH AIR.</p>

  <div class="price-tag">
    <span class="lead">NOW ONLY IN</span>
    <span class="amount">$110</span>
  </div>

  <p class="call-now"><span class="label">CALL NOW:</span> 0400555019</p>

  <h2 class="tasks-bar">TASKS INCLUDED IN PACKAGE ARE:</h2>

  <ul class="task-list">
    <li><svg class="tick" viewBox="0 0 32 26"><ellipse cx="20" cy="12" rx="11" ry="9" fill="#f7941d"/><path d="M2 16 L9 23 L30 2" fill="none" stroke="#111" stroke-width="3"/></svg>Inspection and clean of pads</li>
    <li><svg class="tick" viewBox="0 0 32 26"><ellipse cx="20" cy="12" rx="11" ry="9" fill="#f7941d"/><path d="M2 16 L9 23 L30 2" fill="none" stroke="#111" stroke-width="3"/></svg>Inspection and check float valve, water pump, fan, motor, bearings, drain</li>
    <li><svg class="tick" viewBox="0 0 32 26"><ellipse cx="20" cy="12" rx="11" ry="9" fill="#f7941d"/><path d="M2 16 L9 23 L30 2" fill="none" stroke="#111" stroke-width="3"/></svg>Clean basin</li>
    <li><svg class="tick" viewBox="0 0 32 26"><ellipse cx="20" cy="12" rx="11" ry="9" fill="#f7941d"/><path d="M2 16 L9 23 L30 2" fill="none" stroke="#111" stroke-width="3"/></svg>Supply of bacterial tablet</li>
    <li><svg class="tick" viewBox="0 0 32 26"><ellipse cx="20" cy="12" rx="11" ry="9" fill="#f7941d"/><path d="M2 16 L9 23 L30 2" fill="none" stroke="#111" stroke-width="3"/></svg>Inspect overall condition of unit</li>
    <li><svg class="tick" viewBox="0 0 32 26"><ellipse cx="20" cy="12" rx="11" ry="9" fill="#f7941d"/><path d="M2 16 L9 23 L30 2" fill="none" stroke="#111" stroke-width="3"/></svg>Any repairs if required will be quoted</li>
  </ul>

  <footer class="footer">
    <p class="abn">ABN - 12345678901</p>
    <svg class="mail-icon" viewBox="0 0 34 25"><rect x="0" y="0" width="34" height="25" rx="3" fill="#ffffff"/><path d="M2 3 L17 14 L32 3" fill="none" stroke="#12107a" stroke-width="2.5"/></svg>
    <p class="email">admin@harbourlineplumbing.com.au</p>
    <div class="footer-brand">
      <span class="brand-dot"></span>
      <span><span class="main">HARBOURLINE</span><span class="sub">GAS &amp; PLUMBING</span></span>
    </div>
  </footer>
</main>
</body>
</html>
```